KLV Broadband 1/2 page flyer*

We'd like to have a half page flyer created listing our prices for the plans for wireless internet, our website, phone number, and some quick "eye catching" blips about what we offer. We are a new rural local WISP (Wireless Internet Service Provider) trying to break major ISP monopolies for the farmers in Iowa.URL: https://stsbroadband.com/Phone: (319) 988-1531Our selling points are:No data capsNo lease feesNo activation feesLocally owned and operatedWe have our website running and all the prices listed out there. We're hoping to see Residential/Business prices listed on this flyer. Our colors are Red, White and Blue.I've tried and failed at this. Please see my poor example of the flyer. I've included the PSD file if this will help. I've included our Parent Company logo for any image clarification. We really want to have the contrast in colors, and the Iowa farm life being highlighted. This can be grain elevators, windmills, barns, etc.

Target Market(s)

Rural Iowa Farmers without internet

Industry/Entity Type

Information Technology

Font styles to use
Sans Serif

Colors

Designer to choose colors to be used in the design.

Requirements
Must have
• Prices and eye catchers for sales. Website pricing and eye catchers are provided
Nice to have
• Color flow with the red white and blue schematic of the KLV Broadband logo.
Should not have
• City images, we live in Rural Iowa and farm images are necessary.

```html
<!DOCTYPE html>
<html lang="en">
<head>
<meta charset="utf-8">
<title>KLV Broadband – High Speed Internet Access Flyer</title>
<link href="https://fonts.googleapis.com/css2?family=Open+Sans:wght@400;600;700&family=Roboto:ital,wght@1,500;1,700;1,900&display=swap" rel="stylesheet">
<style>
  :root{
    --blue-deep:#1d3f9a;
    --blue-mid:#1565c8;
    --blue-sky:#3aa0d6;
    --blue-soft:#a8d0e4;
    --blue-plus:#8fc4dc;
    --blue-pale:#c4e8f8;
    --red:#e1222b;
    --red-bright:#e84848;
    --red-dark:#a8121a;
    --pink:#f4a5a5;
    --pink-deep:#ef8c8c;
    --white:#ffffff;
    --ink:#1a1a1a;
    --page:#f2efe9;
  }
  *{margin:0;padding:0;box-sizing:border-box}
  html,body{width:1200px;height:1200px;overflow:hidden;background:var(--page)}
  .flyer{
    position:absolute;left:152px;top:20px;width:990px;height:1280px;
    transform:scale(0.906);transform-origin:0 0;overflow:hidden;
    font-family:"Open Sans",Arial,sans-serif;color:var(--ink);
  }
  .abs{position:absolute}
  .field-photo{left:0;top:0;width:990px;height:1280px;
    background:linear-gradient(180deg,#7aa6d6 0%,#b9d3e8 22%,#dcd9b8 42%,#d8b45a 62%,#c8952e 82%,#8a6420 100%)}
  .stripe-top{left:0;top:0;width:990px;height:9px;background:var(--red)}
  .stripe-bottom{left:600px;top:1266px;width:390px;height:14px;background:var(--red)}
  .inner-panel{left:46px;top:44px;width:898px;height:1184px;border:4px solid rgba(255,255,255,.85);
    background:linear-gradient(180deg,rgba(255,255,255,.55) 0%,rgba(255,255,255,.35) 40%,rgba(255,255,255,.15) 100%)}
  .header-white{left:50px;top:48px;width:890px;height:128px;background:var(--white)}
  .logo-zone{left:50px;top:48px;width:890px;height:140px}
  .brand{left:70px;top:92px;display:flex;align-items:center;gap:14px}
  .brand-dot{width:30px;height:30px;border-radius:50%;background:var(--blue-mid)}
  .brand-name{font-family:"Open Sans",sans-serif;font-weight:600;font-size:40px;color:var(--blue-deep)}
  .headline{left:520px;top:60px;font-family:"Roboto",sans-serif;font-style:italic;font-weight:900;line-height:1}
  .headline .h1{font-size:58px;color:var(--blue-deep);letter-spacing:1px}
  .headline .h2{font-size:40px;color:var(--red);margin-top:4px;letter-spacing:1px}
  .intro{left:90px;top:206px;width:830px;font-family:"Roboto",sans-serif;font-style:italic;font-weight:500;font-size:25px;line-height:32px;color:#111}
  .intro b{font-weight:700}
  .intro .accent{color:var(--blue-mid)}
  .perks-band{left:27px;top:281px;width:613px;height:129px;
    background:linear-gradient(90deg,var(--blue-deep) 0%,var(--blue-mid) 55%,rgba(21,101,200,0) 100%)}
  .perks{left:115px;top:296px;list-style:none}
  .perks li{display:flex;align-items:center;gap:14px;height:31px;font-family:"Roboto",sans-serif;font-style:italic;font-weight:700;font-size:25px;color:var(--white)}
  .section-title{font-family:"Roboto",sans-serif;font-style:italic;font-weight:900;font-size:33px;color:var(--blue-mid);
    -webkit-text-stroke:1px var(--white);paint-order:stroke fill;text-shadow:0 0 3px #fff}
  .residential{left:677px;top:372px}
  .business{left:732px;top:1148px;color:var(--red)}
  .plan-head{font-family:"Roboto",sans-serif;font-style:italic;font-weight:700;font-size:22px;padding-left:14px;display:flex;align-items:center}
  .plan-body{padding:12px 4px 0 14px;font-size:19px;line-height:25px;letter-spacing:-0.2px;overflow:hidden}
  .plan-body .speed{font-weight:700}
  .plan-body ul{list-style:none}
  .plan-body li{position:relative;padding-left:16px}
  .plan-body li::before{content:"";position:absolute;left:1px;top:10px;width:6px;height:6px;border-radius:50%;background:var(--bullet,var(--blue-sky))}
  .plan-body small{font-size:15px}
  .res-basic-head{left:56px;top:490px;width:291px;height:38px;background:var(--blue-pale);color:#111}
  .res-basic-body{left:56px;top:528px;width:291px;height:207px;background:rgba(255,255,255,.9)}
  .res-plus-head{left:347px;top:454px;width:291px;height:37px;background:var(--blue-plus);color:#111}
  .res-plus-body{left:347px;top:491px;width:291px;height:244px;background:var(--blue-soft);padding-top:49px}
  .res-prem-head{left:638px;top:417px;width:298px;height:37px;background:var(--blue-deep);color:var(--white)}
  .res-prem-body{left:638px;top:454px;width:298px;height:281px;background:var(--blue-sky);color:var(--white);padding-top:74px;--bullet:var(--white)}
  .biz-basic-body{left:56px;top:742px;width:290px;height:292px;background:rgba(255,255,255,.9);--bullet:var(--red)}
  .biz-basic-head{left:56px;top:1034px;width:290px;height:36px;background:var(--pink-deep);color:var(--white)}
  .biz-big-body{left:346px;top:742px;width:290px;height:328px;background:var(--pink);--bullet:var(--red)}
  .biz-big-head{left:346px;top:1070px;width:290px;height:37px;background:var(--red-bright);color:var(--white)}
  .biz-xl-body{left:636px;top:742px;width:300px;height:366px;background:var(--red-bright);color:var(--white);--bullet:var(--white)}
  .biz-xl-head{left:636px;top:1108px;width:300px;height:37px;background:var(--red-dark);color:var(--white);padding-left:28px}
  .farm-art{left:66px;top:1090px;width:262px;height:100px;border-radius:6px;
    background:linear-gradient(90deg,#d8402f 0%,#e7d9b4 45%,#e0b43a 70%,#6c6c6c 100%);opacity:.85}
  .footer-band{left:0;top:1187px}
  .contact{left:130px;top:1204px;font-family:"Roboto",sans-serif;font-style:italic;font-weight:900;font-size:27px;color:var(--white);line-height:33px}
  .contact div{display:flex;align-items:center;gap:14px}
</style>
</head>
<body>
<div class="flyer">
  <div class="abs field-photo" role="img" aria-label="Photograph of a golden Iowa wheat field under a blue sky"></div>
  <div class="abs stripe-top"></div>
  <div class="abs inner-panel"></div>
  <div class="abs header-white"></div>
  <svg class="abs logo-zone" width="890" height="140" viewBox="0 0 890 140" aria-hidden="true">
    <polygon points="3,6 375,6 440,128 3,128" fill="#cfe3f3"/>
  </svg>
  <div class="abs brand"><span class="brand-dot"></span><span class="brand-name">KLV Broadband</span></div>
  <div class="abs headline"><div class="h1">HIGH SPEED</div><div class="h2">INTERNET ACCESS</div></div>

  <p class="abs intro"><b>We are <span class="accent">locally owned</span> WISP</b> serving the local communities in Eastern Iowa. Our service is budget friendly and state of the art!</p>

  <div class="abs perks-band"></div>
  <ul class="abs perks">
    <li><svg width="30" height="30" viewBox="0 0 30 30"><circle cx="14" cy="16" r="11" fill="none" stroke="#fff" stroke-width="2.5"/><path d="M8 15l6 6L27 5" fill="none" stroke="#fff" stroke-width="2.8"/></svg>No data caps</li>
    <li><svg width="30" height="30" viewBox="0 0 30 30"><circle cx="14" cy="16" r="11" fill="none" stroke="#fff" stroke-width="2.5"/><path d="M8 15l6 6L27 5" fill="none" stroke="#fff" stroke-width="2.8"/></svg>No lease fees</li>
    <li><svg width="30" height="30" viewBox="0 0 30 30"><circle cx="14" cy="16" r="11" fill="none" stroke="#fff" stroke-width="2.5"/><path d="M8 15l6 6L27 5" fill="none" stroke="#fff" stroke-width="2.8"/></svg>No activation fees</li>
  </ul>

  <div class="abs section-title residential">RESIDENTIAL</div>

  <svg class="abs" style="left:312px;top:454px" width="36" height="37" aria-hidden="true"><polygon points="36,0 36,37 0,37" fill="#1e8fd0"/></svg>
  <svg class="abs" style="left:603px;top:417px" width="36" height="37" aria-hidden="true"><polygon points="36,0 36,37 0,37" fill="#1e8fd0"/></svg>

  <div class="abs plan-head res-basic-head">KLVB Basic Plan</div>
  <div class="abs plan-body res-basic-body">
    <div class="speed">50Mbps</div>
    <ul><li>2-4, social media, Lite Online HD Streaming, Music, Photos, Lite HD Online Gaming.</li>
    <li><b>$40</b>/Month</li><li><b>$100</b> Installation</li></ul>
  </div>
  <div class="abs plan-head res-plus-head">KLVB Plus Plan</div>
  <div class="abs plan-body res-plus-body">
    <div class="speed">70Mbps</div>
    <ul><li>Multiple users, HD Streaming,active browsing, HD Online Gaming, Smart-home Cloud Access.</li>
    <li><b>$50</b>/Month</li><li><b>$100</b> Installation</li></ul>
  </div>
  <div class="abs plan-head res-prem-head">KLVB Premium Plan</div>
  <div class="abs plan-body res-prem-body">
    <div class="speed">150Mbps+ (COMING SOON!)</div>
    <ul><li>Multiple users, 4K Streaming 4K Video Publishing, 4K Online Gaming, Smart-home Cloud Access.</li>
    <li><b>$100</b>/Month</li><li><b>$100</b> Installation</li></ul>
  </div>

  <div class="abs plan-body biz-basic-body">
    <div class="speed">50Mbps</div>
    <ul><li>Small Business (1-3 person)</li>
    <li>Active browsing, Email, 1-3 Person Video Conferencing, VOIP Phone, Reduced Lag on Data Transfers and Increased Productivity.</li>
    <li><b>$100</b>/Month</li><li><b>$100</b> Installation</li></ul>
  </div>
  <div class="abs plan-head biz-basic-head">KLVB Basic Business</div>
  <div class="abs plan-body biz-big-body">
    <div class="speed">100Mbps</div>
    <ul><li>Small Business <small>(2-10 person)</small></li>
    <li>Active browsing, Email, Multi-user HD Video Conferencing,VOIP Phone, Reduced Lag on Data Transfers and Increased Productivity.</li>
    <li><b>$150</b>/Month</li><li><b>$100</b> Installation</li></ul>
  </div>
  <svg class="abs" style="left:594px;top:1070px" width="44" height="37" aria-hidden="true"><polygon points="0,0 44,0 44,37" fill="#c01820"/></svg>
  <div class="abs plan-head biz-big-head">KLVB Big Business</div>
  <div class="abs plan-body biz-xl-body">
    <div class="speed">300Mbps</div>
    <ul><li>Small Business <small>(10-50 person)</small></li>
    <li>Active browsing, Email, Multi-user 4K Video Conferencing, VOIP Phone, Reduced Lag on Data Transfers and Increased Productivity.</li>
    <li><b>$225</b>/Month</li><li><b>$100</b> Installation</li></ul>
  </div>
  <svg class="abs" style="left:598px;top:1108px" width="40" height="37" aria-hidden="true"><polygon points="0,0 40,0 40,37" fill="#8a0e14"/></svg>
  <div class="abs plan-head biz-xl-head">KLVB Busines XL</div>

  <div class="abs section-title business">BUSINESS</div>

  <div class="abs farm-art" role="img" aria-label="Illustration of a red barn with a wireless signal, crop rows and a yellow tractor"></div>

  <svg class="abs footer-band" width="640" height="93" viewBox="0 0 640 93" aria-hidden="true">
    <defs><linearGradient id="footerBlue" x1="0" x2="1"><stop offset="0" stop-color="#1d3f9a"/><stop offset="1" stop-color="#1577cc"/></linearGradient></defs>
    <polygon points="27,0 550,0 640,93 27,93" fill="url(#footerBlue)"/>
  </svg>
  <div class="abs stripe-bottom"></div>
  <div class="abs contact">
    <div><svg width="28" height="28" viewBox="0 0 24 24"><path d="M6.6 10.8a15 15 0 006.6 6.6l2.2-2.2a1 1 0 011-.25 11 11 0 003.6.6 1 1 0 011 1V20a1 1 0 01-1 1A17 17 0 013 4a1 1 0 011-1h3.5a1 1 0 011 1 11 11 0 00.6 3.6 1 1 0 01-.25 1z" fill="#fff"/></svg>(555) 402-7786</div>
    <div><svg width="28" height="28" viewBox="0 0 24 24" fill="none" stroke="#fff" stroke-width="2"><circle cx="12" cy="12" r="10"/><ellipse cx="12" cy="12" rx="4.5" ry="10"/><path d="M2 12h20M4 6.5h16M4 17.5h16"/></svg>klvbroadband.example</div>
  </div>
</div>
</body>
</html>
```